teaching love. a joyful state of being.

adding value to ones circumstance through the teachings of neutralization. quote for back of card: "and then it happens... One day you wake up and you're in this place. You are in this place where everything is right. Your heart is calm. Your soul is lit. Your thoughts are positive. Your vision is clear. Your faith is stronger than ever. And you are at peace. At peace with where you have been. At peace with what you've been through. And at peace with where you're headed." -unknown

Target Market(s)

spiritual, awakening, inspiration, motivation, gratefulness, oneness, peace, positive mindset,

Contact Information for Business Card

front: one line message from quote

Logo Text

up to suggestions

Font styles to use
Serif
Sans Serif
Script

Colors

Designer to choose colors to be used in the design.

Requirements
Must have
• entire quote on one side of card
Nice to have
• simple, and to the point
Should not have
• elaborated designs

```html
<!DOCTYPE html>
<html lang="en">
<head>
<meta charset="utf-8">
<title>Calm Within – Business Card</title>
<link rel="stylesheet" href="https://fonts.googleapis.com/css2?family=Noto+Sans:wght@400;500&family=Noto+Serif:wght@400&display=swap">
<style>
  :root {
    --red: #e8141b;
    --black: #111111;
    --white: #ffffff;
    --ink: #4a4a4a;
    --logo-tint: #f4b4ae;
    --backdrop: #e6e6e4;
  }
  * { margin: 0; padding: 0; box-sizing: border-box; }
  html, body {
    width: 1200px; height: 768px; overflow: hidden;
    background: var(--backdrop);
  }
  .canvas {
    position: relative; width: 1200px; height: 768px;
  }
  .card {
    position: absolute; top: 224px;
    width: 560px; height: 320px;
    background: var(--white);
    box-shadow: 0 6px 18px rgba(0,0,0,.18);
    overflow: hidden;
  }
  .card--back { left: 27px; }
  .card--front { left: 613px; }
  .card__shapes { position: absolute; inset: 0; width: 560px; height: 320px; }

  /* Back */
  .quote {
    position: absolute; top: 70px; left: 28px; right: 28px;
    font-family: "Noto Sans", sans-serif; font-weight: 500;
    font-size: 13.5px; line-height: 19px; letter-spacing: .2px;
    color: var(--red); text-align: center;
  }
  .quote__credit { display: block; margin-top: 2px; font-size: 12px; }

  /* Front */
  .logo {
    position: absolute; left: 40px; top: 62px; width: 230px;
    text-align: center;
  }
  .logo__mark {
    display: block; width: 56px; height: 56px; margin: 0 auto 14px;
    border-radius: 50%; background: var(--logo-tint);
  }
  .logo__name {
    font-family: "Noto Serif", serif; font-size: 34px; line-height: 1;
    color: var(--logo-tint);
  }
  .person {
    position: absolute; right: 26px; top: 150px; width: 240px;
    text-align: center;
  }
  .person__name {
    font-family: "Noto Serif", serif; font-size: 24px; color: var(--ink);
    line-height: 1.1;
  }
  .person__role {
    font-family: "Noto Serif", serif; font-size: 13px; color: var(--red);
  }
  .contact {
    position: absolute; left: 40px; top: 220px; list-style: none;
    font-family: "Noto Serif", serif; font-size: 13px; color: var(--black);
  }
  .contact__item { display: flex; align-items: center; gap: 8px; height: 20px; }
  .contact__icon { width: 14px; height: 14px; flex: none; }
  .address {
    position: absolute; left: 372px; top: 220px; display: flex; gap: 8px;
    font-family: "Noto Serif", serif; font-size: 13px; line-height: 17px;
    color: var(--black);
  }
  .address__icon { width: 14px; height: 18px; flex: none; margin-top: 6px; }
</style>
</head>
<body>
<main class="canvas">

  <section class="card card--back" aria-label="Card back">
    <svg class="card__shapes" viewBox="0 0 560 320" aria-hidden="true">
      <g class="ribbons" transform="translate(246 0)">
        <polygon points="12,0 32,0 22,56 0,48" fill="var(--red)"/>
        <polygon points="36,0 56,0 46,56 24,48" fill="var(--black)"/>
        <polygon points="60,0 80,0 70,56 48,48" fill="var(--red)"/>
      </g>
      <rect x="0" y="282" width="560" height="20" fill="var(--red)"/>
    </svg>
    <p class="quote">“And then it happens… One day you wake up and you’re in this place. You are in this place where everything is right. Your heart is calm. Your soul is lit. Your thoughts are positive. Your vision is clear. Your faith is stronger than ever. And you are at peace. At peace with where you have been. At peace with what you’ve been through. And at peace with where you’re headed.”<span class="quote__credit">– unknown</span></p>
  </section>

  <section class="card card--front" aria-label="Card front">
    <svg class="card__shapes" viewBox="0 0 560 320" aria-hidden="true">
      <g class="ribbons" transform="translate(420 0)">
        <polygon points="14,0 36,0 24,82 0,72" fill="var(--red)"/>
        <polygon points="40,0 62,0 50,82 26,72" fill="var(--black)"/>
        <polygon points="66,0 88,0 76,82 52,72" fill="var(--red)"/>
      </g>
      <line x1="36" y1="205" x2="540" y2="205" stroke="var(--red)" stroke-width="2"/>
      <polygon points="0,298 318,298 308,320 0,320" fill="var(--black)"/>
      <polygon points="324,320 344,274 560,274 560,320" fill="var(--red)"/>
    </svg>

    <div class="logo">
      <span class="logo__mark"></span>
      <p class="logo__name">Calm Within</p>
    </div>

    <div class="person">
      <p class="person__name">Amara Wanjiru</p>
      <p class="person__role">Manager</p>
    </div>

    <ul class="contact">
      <li class="contact__item">
        <svg class="contact__icon" viewBox="0 0 14 14" aria-hidden="true"><rect x="3.5" y="0.8" width="7" height="12.4" rx="1.4" fill="none" stroke="currentColor" stroke-width="1.2"/><line x1="6" y1="11" x2="8" y2="11" stroke="currentColor"/></svg>
        +254 700 123 456
      </li>
      <li class="contact__item">
        <svg class="contact__icon" viewBox="0 0 14 14" aria-hidden="true"><rect x="0.8" y="3" width="12.4" height="8.5" fill="none" stroke="currentColor" stroke-width="1.2"/><polyline points="0.8,3 7,8 13.2,3" fill="none" stroke="currentColor" stroke-width="1.2"/></svg>
        amara.wanjiru@example.com
      </li>
      <li class="contact__item">
        <svg class="contact__icon" viewBox="0 0 14 14" aria-hidden="true"><circle cx="7" cy="7" r="5.8" fill="none" stroke="currentColor" stroke-width="1.2"/><line x1="1.2" y1="7" x2="12.8" y2="7" stroke="currentColor"/><ellipse cx="7" cy="7" rx="2.6" ry="5.8" fill="none" stroke="currentColor"/></svg>
        www.yourdomain.com
      </li>
    </ul>

    <div class="address">
      <svg class="address__icon" viewBox="0 0 14 18" aria-hidden="true"><path d="M7 17 C3 11 1 8.5 1 6.5 A6 6 0 0 1 13 6.5 C13 8.5 11 11 7 17Z" fill="none" stroke="currentColor" stroke-width="1.2"/><circle cx="7" cy="6.5" r="2" fill="none" stroke="currentColor" stroke-width="1.2"/></svg>
      <p>Street Name, Suit 1234<br>State, Zip Code, Country</p>
    </div>
  </section>

</main>
</body>
</html>
```